Cleaning Business, Premium Services

We need a DL size flyer designs for a cleaning business based in Melbourne, Australia called Bright Nest Domestic Cleaning and the slogan is More Time for Life! We would like to keep the corporate colour of blue and red. Our main services are home and office cleaning, window cleaning and carpet cleaning. We are targeting the high net worth clients ie we provide premium services. The final design should communicate quality of service in terms of professionalism and reliability of staff. We would also like a new and creative slogan for the brand. The company's current logo is attached.
Updates

Project Deadline Extended
Reason: To allow adjustment to be made.

Target Market(s)

High net worth clients, high income clients, corporate executives, clients with big houses and mansions

Industry/Entity Type

Business

Requirements
Must have
• Company's name, corporate colour blue and red | Contact : Gareth Weller | Mobile: 0412-586-104 | Email: bnd.kewvale@mailory.net | A: P O Box 418, Tarrin Heights VIC 3162
Nice to have
• New slogan. Different corporate colours

```html
<!DOCTYPE html>
<html lang="en">
<head>
<meta charset="utf-8">
<title>Bright Nest Domestic Cleaning – DL Flyer</title>
<link rel="stylesheet" href="https://fonts.googleapis.com/css2?family=Arimo:wght@400;700&display=swap">
<style>
  :root {
    --page-bg: #e9e7e4;
    --brand-blue: #1b4fa0;
    --bar-blue: #1a7fd9;
    --brand-red: #e0161c;
    --white: #ffffff;
    --sky-top: #9fb0c0;
    --city-mid: #5f6467;
    --room-dark: #2c2320;
    --desk-brown: #4a2a22;
  }
  * { box-sizing: border-box; margin: 0; padding: 0; }
  html, body {
    width: 1200px; height: 1000px; overflow: hidden;
    background: var(--page-bg);
    font-family: "Arimo", Arial, sans-serif;
  }
  .flyer {
    position: absolute; left: 40px; top: 228px;
    width: 1120px; height: 543px; overflow: hidden;
    box-shadow: 0 6px 18px rgba(0,0,0,0.25);
  }
  .office-photo {
    position: absolute; inset: 0;
    background:
      linear-gradient(180deg, var(--sky-top) 0%, #7d8791 22%, var(--city-mid) 40%, #8e8b83 52%, #5a4a44 62%, var(--desk-brown) 78%, var(--room-dark) 100%);
  }
  .services-map {
    position: absolute; inset: 0; width: 100%; height: 100%;
  }
  .service-label {
    fill: var(--white); font-family: "Arimo", Arial, sans-serif;
    font-size: 17px; letter-spacing: 0.5px; text-anchor: middle;
  }
  .service-label--main { font-size: 20px; font-weight: 700; }
  .brand-panel {
    position: absolute; left: 0; top: 74px;
    width: 370px; height: 155px;
    background: var(--white);
    border-radius: 0 78px 78px 0;
    display: flex; align-items: center; gap: 16px;
    padding-left: 36px;
  }
  .brand-square {
    width: 44px; height: 44px; background: var(--brand-blue); flex: none;
  }
  .brand-name {
    color: var(--brand-blue); font-weight: 700; line-height: 1.05;
  }
  .brand-name__main { display: block; font-size: 40px; letter-spacing: -0.5px; }
  .brand-name__sub { display: block; font-size: 21px; }
  .brand-slogan {
    display: block; margin-top: 6px;
    color: var(--brand-red); font-size: 16px; font-weight: 700;
  }
  .contact-bar {
    position: absolute; left: 0; bottom: 0; width: 100%; height: 29px;
    background: var(--bar-blue); color: var(--white);
    font-size: 14.5px; font-weight: 700;
    display: flex; align-items: center; justify-content: center;
    letter-spacing: 0.1px; white-space: nowrap;
  }
</style>
</head>
<body>
  <main class="flyer">
    <div class="office-photo" role="img" aria-label="Photo of a clean high-rise corner office with a wooden desk, computer, black mesh chairs and floor-to-ceiling windows over a city skyline"></div>

    <svg class="services-map" viewBox="0 0 883 428" preserveAspectRatio="none">
      <g class="connector-lines" stroke="#ffffff" stroke-width="1.3" fill="none">
        <line x1="556" y1="107" x2="702" y2="128"/>
        <line x1="488" y1="294" x2="716" y2="176"/>
        <line x1="675" y1="278" x2="740" y2="204"/>
        <line x1="783" y1="270" x2="776" y2="206"/>
      </g>
      <g class="service-circles" stroke="#ffffff" stroke-width="1.5" fill="rgba(20,16,14,0.18)">
        <circle cx="502" cy="103" r="54"/>
        <circle cx="437" cy="317" r="54"/>
        <circle cx="650" cy="328" r="54"/>
        <circle cx="800" cy="311" r="42"/>
      </g>
      <circle class="service-circle--main" cx="768" cy="138" r="68" fill="rgba(20,16,14,0.12)" stroke="#e0161c" stroke-width="3.5"/>
      <text class="service-label" x="502" y="109">WINDOWS</text>
      <text class="service-label service-label--main" x="768" y="145">CLEANING</text>
      <text class="service-label" x="437" y="323">CARPETS</text>
      <text class="service-label" x="650" y="314">HOME</text>
      <text class="service-label" x="650" y="333">AND</text>
      <text class="service-label" x="650" y="352">OFFICE</text>
      <text class="service-label" x="800" y="308" style="font-size:23px">AND</text>
      <text class="service-label" x="800" y="328">MORE</text>
    </svg>

    <header class="brand-panel">
      <span class="brand-square"></span>
      <div class="brand-text">
        <h1 class="brand-name">
          <span class="brand-name__main">Bright Nest</span>
          <span class="brand-name__sub">Domestic Cleaning</span>
        </h1>
        <span class="brand-slogan">More Time for Life!</span>
      </div>
    </header>

    <footer class="contact-bar">
      CONTACT : GARETH WELLER | MOBILE: 0412-586-104 | EMAIL: BND.KEWVALE@MAILORY.NET | A: P O BOX 418, TARRIN HEIGHTS VIC 3162
    </footer>
  </main>
</body>
</html>
```